Thornbury Building Company - Card Design

I am looking to use the logo designs that you already did for me to develop a business card. I would like the card to have a black background and be double sided. I want white and green logo and text. I have attached an inspiration photo of a look that I like. I would like to use the Vertical Logo attached to take up the full front side of the card. On the back where I have my name and information, I would like to have the horizontal logo or maybe even just the image of the 'A' and trees without the text. I am open, but I am looking for something clean and simple and I want the green to really pop! Additional files can be found under Design #: 58302946

Target Market(s)

Homeowners

Industry/Entity Type

Construction

Contact Information for Business Card

Name: Marcus Thornbury, Title: Project Manager, Phone: 555.274.8136, Email: thornburybuildingcompany@mailvesta.com, address: 487 Larkspur Ln, Felton, CA 95033, Lic# 2468317

Colors
00AB8E
00BBA5
67D7C9
C6EFE9
E9F9F6

Requirements
Nice to have
• I would like to see the logos that I have already got from ArtLoomHub, though I am open to new ones

```html
<!DOCTYPE html>
<html lang="en">
<head>
<meta charset="utf-8">
<title>Thornbury Building Company – Business Card</title>
<link rel="stylesheet" href="https://fonts.googleapis.com/css2?family=Montserrat:wght@400;500;700&display=swap">
<style>
  :root {
    --stage: #2b2b2b;
    --card: #1b1b1b;
    --green: #6db847;
    --white: #ffffff;
    --muted: #e8e8e8;
  }
  * { box-sizing: border-box; margin: 0; padding: 0; }
  html, body {
    width: 1200px; height: 988px; overflow: hidden;
    background: var(--stage);
    font-family: "Montserrat", sans-serif;
  }
  .canvas { position: relative; width: 1200px; height: 988px; }
  .card {
    position: absolute; left: 220px; width: 760px; height: 434px;
    background: var(--card); border-radius: 22px; overflow: hidden;
    box-shadow: 0 12px 30px rgba(0,0,0,.45);
  }
  .card--front { top: 40px; }
  .card--back { top: 514px; }

  /* Wordmark stand-in */
  .wordmark { position: absolute; display: flex; align-items: center; gap: 18px; color: var(--white); font-weight: 700; }
  .wordmark__square { background: var(--green); flex: none; }
  .wordmark__name { line-height: 1.05; text-transform: uppercase; }
  .wordmark__name span { display: block; }
  .card--front .wordmark { left: 50%; top: 50%; transform: translate(-50%, -50%); }
  .card--front .wordmark__square { width: 64px; height: 64px; }
  .card--front .wordmark__name { font-size: 44px; letter-spacing: 2px; }
  .card--front .wordmark__name .wordmark__sub { font-size: 19px; letter-spacing: 6px; }
  .card--back .wordmark { right: 48px; top: 44px; gap: 12px; }
  .card--back .wordmark__square { width: 36px; height: 36px; }
  .card--back .wordmark__name { font-size: 25px; letter-spacing: 1px; }
  .card--back .wordmark__name .wordmark__sub { font-size: 11px; letter-spacing: 3.4px; }

  .rule { position: absolute; height: 1px; background: var(--green); }
  .rule--top { left: 48px; right: 48px; top: 132px; }
  .rule--contact { left: 48px; width: 300px; top: 232px; }

  .person { position: absolute; left: 48px; top: 170px; }
  .person__name { color: var(--green); font-weight: 700; font-size: 26px; letter-spacing: 1px; text-transform: uppercase; }
  .person__title { color: var(--white); font-size: 15px; font-weight: 500; margin-top: 2px; }

  .contact { position: absolute; left: 48px; top: 248px; list-style: none; color: var(--muted); font-size: 15px; }
  .contact li { display: flex; align-items: center; gap: 10px; margin-bottom: 8px; }
  .contact svg { width: 16px; height: 16px; fill: var(--green); flex: none; }

  .address { position: absolute; right: 48px; top: 168px; text-align: right; color: var(--white); font-size: 16px; line-height: 1.35; }

  .band { position: absolute; left: 0; bottom: 0; width: 760px; height: 70px; }
  .license { position: absolute; right: 92px; bottom: 22px; width: 170px; text-align: center; color: #1b1b1b; font-size: 15px; font-weight: 500; }
</style>
</head>
<body>
<main class="canvas">

  <section class="card card--front" aria-label="Card front">
    <div class="wordmark">
      <div class="wordmark__square"></div>
      <div class="wordmark__name"><span>Thornbury</span><span class="wordmark__sub">Building Company</span></div>
    </div>
  </section>

  <section class="card card--back" aria-label="Card back">
    <div class="wordmark">
      <div class="wordmark__square"></div>
      <div class="wordmark__name"><span>Thornbury</span><span class="wordmark__sub">Building Company</span></div>
    </div>

    <div class="rule rule--top"></div>

    <div class="person">
      <h1 class="person__name">Marcus Thornbury</h1>
      <p class="person__title">Project Manager</p>
    </div>

    <div class="rule rule--contact"></div>

    <ul class="contact">
      <li>
        <svg viewBox="0 0 24 24" aria-hidden="true"><path d="M6.6 10.8a15.1 15.1 0 0 0 6.6 6.6l2.2-2.2a1 1 0 0 1 1-.25 11.4 11.4 0 0 0 3.6.57 1 1 0 0 1 1 1V20a1 1 0 0 1-1 1A17 17 0 0 1 3 4a1 1 0 0 1 1-1h3.5a1 1 0 0 1 1 1c0 1.25.2 2.45.57 3.57a1 1 0 0 1-.25 1z"/></svg>
        555.274.8136
      </li>
      <li>
        <svg viewBox="0 0 24 24" aria-hidden="true"><path d="M3 5h18a1 1 0 0 1 1 1v12a1 1 0 0 1-1 1H3a1 1 0 0 1-1-1V6a1 1 0 0 1 1-1zm9 7.5L20.5 7h-17z"/></svg>
        thornburybuildingcompany@mailvesta.com
      </li>
    </ul>

    <address class="address" style="font-style:normal">487 Larkspur Ln, Felton<br>CA 95033</address>

    <svg class="band" viewBox="0 0 760 70" aria-hidden="true">
      <polygon points="0,12 490,12 474,70 0,70" fill="var(--green)"/>
      <polygon points="500,12 680,12 664,58 484,58" fill="var(--white)"/>
      <polygon points="690,12 760,12 760,58 674,58" fill="var(--green)"/>
    </svg>
    <p class="license">Lic# 2468317</p>
  </section>

</main>
</body>
</html>
```